EB-5 Regional Center needs a Web design

Harlow Ridge Financial Partners is an expanding EB-r regional center. We have been successful in sponsoring multiple projects of third-party developers and placing EB-5, B-1, and Private Investments into multiple projects.

We are now partnering directly with project developers in the energy and healthcare to raise foreign capital for projects in those industries. The foreign capital is used as project equity and our collective balance sheets are used to guarantee debt to complete the funding of the projects.

We need a web site where we can post our company credentials, the bios of each partner, a document page for each of our projects where we can post specific project related documents which foreign investors can read, and we will need a section where foreign investors can fill out investor forms confirming that they are qualified investors and leaving their contact so that our agents and executives can make contact.

The final design should reflect the exceptional experience of the partners and our financial strength and stability.

We do have a logo we would want to use on the web design.

Target Market(s)

EB-5 Investors, B-1 Investors, Private Equity and other investors seeking quality investment in job creating US projects.

Coding

Number of Pages Required

5+ page

Font styles to use
Sans Serif

Requirements
Must have
• Pages to display company info, partner bios, projects completed, and a projects in-process page where we can post documents and info on projects for which we are seeking foreign investment. We also need a section where investors can enter their qualifying personal information and leave contact information for us.

```html
<!DOCTYPE html>
<html lang="en">
<head>
<meta charset="utf-8">
<title>Harlow Ridge Financial Partners</title>
<link rel="stylesheet" href="https://fonts.googleapis.com/css2?family=Montserrat:wght@400;600;700&family=Open+Sans:wght@400;600&family=Ubuntu:wght@400;500&display=swap">
<style>
:root{
  --ink:#2e2e2e;
  --text:#444;
  --muted:#6a6a6a;
  --white:#fff;
  --dark:#4a4a4a;
  --darker:#3a3a3a;
  --light:#e8e8e8;
  --black:#050505;
  --gray-btn:#a9a9a9;
  --field-label:#333;
}
*{margin:0;padding:0;box-sizing:border-box}
html,body{width:1200px;height:3503px;overflow:hidden}
body{position:relative;background:var(--white);font-family:"Open Sans",Arial,sans-serif;color:var(--text)}
.abs{position:absolute}
.center{left:0;width:1200px;text-align:center}
.heading{font-family:"Ubuntu",Arial,sans-serif;font-weight:500;font-size:34px;color:var(--ink);letter-spacing:.2px}
.rule{position:absolute;left:572px;width:56px;height:3px;background:var(--ink)}

/* hero */
.hero{position:absolute;left:0;top:0;width:1200px;height:782px;
  background:
    radial-gradient(ellipse 300px 90px at 18% 66%,rgba(235,235,235,.75),transparent 70%),
    radial-gradient(ellipse 360px 110px at 80% 62%,rgba(225,225,225,.7),transparent 70%),
    radial-gradient(ellipse 260px 80px at 50% 78%,rgba(210,210,210,.6),transparent 70%),
    radial-gradient(ellipse 420px 220px at 72% 28%,rgba(150,150,150,.5),transparent 70%),
    radial-gradient(ellipse 380px 200px at 12% 34%,rgba(130,130,130,.45),transparent 70%),
    linear-gradient(180deg,#383838 0%,#555 18%,#2c2c2c 40%,#5a5a5a 58%,#3a3a3a 74%,#626262 100%)}
.brand{position:absolute;left:74px;top:28px;display:flex;align-items:center;gap:12px}
.brand-dot{width:34px;height:34px;border-radius:50%;background:var(--white)}
.brand-name{font-family:"Montserrat",Arial,sans-serif;font-weight:600;font-size:22px;color:var(--white);letter-spacing:.5px;line-height:1.1}
.brand-sub{display:block;font-weight:600;font-size:13px;letter-spacing:2px}
.nav{position:absolute;top:42px;right:58px;display:flex;gap:42px}
.nav a{font-family:"Open Sans",Arial,sans-serif;font-size:15px;color:var(--white);text-decoration:none;position:relative}
.nav a.active:after{content:"";position:absolute;left:0;right:0;bottom:-12px;height:2px;background:#cfcfcf}
.welcome{top:316px;font-family:"Montserrat",Arial,sans-serif;font-size:34px;letter-spacing:6px;color:var(--white)}
.hero-title{top:356px;font-family:"Montserrat",Arial,sans-serif;font-weight:700;font-size:54px;line-height:52px;color:var(--white)}
.btn-hero{left:506px;top:479px;width:178px;height:52px;border-radius:26px;background:var(--gray-btn);color:var(--white);font-family:"Ubuntu",Arial,sans-serif;font-weight:500;font-size:17px;line-height:52px;text-align:center}
.dots{left:1114px;top:337px;display:flex;flex-direction:column;gap:9px}
.dots span{width:14px;height:14px;border-radius:50%;background:var(--white)}
.dots span.on{background:transparent;border:2px solid var(--white)}

/* about */
.about-img{left:163px;top:806px;width:374px;height:368px;border-radius:6px;
  background:
    radial-gradient(ellipse 90px 120px at 45% 55%,rgba(240,240,240,.55),transparent 70%),
    radial-gradient(ellipse 70px 150px at 70% 60%,rgba(200,200,200,.45),transparent 70%),
    radial-gradient(ellipse 120px 60px at 50% 15%,rgba(230,230,230,.7),transparent 70%),
    linear-gradient(165deg,#8a8a8a 0%,#3a3a3a 35%,#1e1e1e 60%,#5a5a5a 85%,#9a9a9a 100%)}
.about-head{left:560px;width:500px;top:822px;text-align:center}
.about-text{left:550px;width:520px;top:894px;text-align:center;font-size:16.5px;line-height:26px;color:var(--text)}
.about-text p+p{margin-top:12px}
.btn-outline{border:2px solid var(--ink);border-radius:30px;color:var(--ink);font-family:"Ubuntu",Arial,sans-serif;font-weight:500;text-align:center}

/* projects */
.projects{position:absolute;left:0;top:1254px;width:1200px;height:620px;background:var(--dark)}
.card{position:absolute;overflow:hidden;color:var(--white);text-align:center;box-shadow:0 4px 14px rgba(0,0,0,.45)}
.card .cap-title{position:absolute;left:0;right:0;font-family:"Ubuntu",Arial,sans-serif;font-weight:500;font-size:19px}
.card .cap-text{position:absolute;left:30px;right:30px;font-size:13px;line-height:20px}
.arrow{font-family:"Open Sans",Arial,sans-serif;font-size:54px;line-height:1;color:#9a9a9a}

/* partners */
.partners{position:absolute;left:0;top:1871px;width:1200px;height:428px;background:var(--light)}
.frame{position:absolute;border:2px solid #9a9a9a;background:var(--light)}
.frame .photo{position:absolute;left:10px;top:10px;right:10px;bottom:10px}
.p-name{font-family:"Ubuntu",Arial,sans-serif;font-weight:500;font-size:19px;color:var(--ink)}
.p-text{font-size:12.5px;line-height:20.5px;color:#555;width:245px}

/* testimonial */
.quote-text{top:2490px;left:230px;width:740px;text-align:center;font-family:Arial,Helvetica,sans-serif;font-size:18.5px;line-height:31px;color:#555}
.circle-arrow{width:46px;height:46px;border-radius:50%;background:#5a5a5a}
.btn-black{background:var(--black);color:var(--white);border-radius:26px;font-family:Arial,Helvetica,sans-serif;font-weight:700;font-size:14px;text-align:center}

/* contact */
.contact{position:absolute;left:0;top:2789px;width:1200px;height:520px;
  background:
    radial-gradient(ellipse 160px 260px at 8% 70%,rgba(90,90,90,.55),transparent 70%),
    radial-gradient(ellipse 180px 280px at 92% 70%,rgba(80,80,80,.55),transparent 70%),
    radial-gradient(ellipse 500px 120px at 50% 8%,rgba(245,245,245,.8),transparent 70%),
    linear-gradient(180deg,#e6e6e6 0%,#c4c4c4 25%,#a6a6a6 55%,#8a8a8a 80%,#9c9c9c 100%)}
.field{position:absolute;background:var(--white);font-family:Arial,Helvetica,sans-serif;font-size:12px;color:var(--field-label);padding:20px 18px}
.footer-nav{top:3370px;display:flex;justify-content:center;gap:42px}
.footer-nav a{color:var(--white);text-decoration:none;font-family:"Open Sans",Arial,sans-serif;font-size:15px}
.social{top:3447px;left:550px;display:flex;gap:32px}
.social span{width:18px;height:18px;border-radius:50%;background:var(--white)}
</style>
</head>
<body>

<section class="hero" role="img" aria-label="Black and white photo of snow-covered mountain peaks above clouds"></section>
<div class="brand"><span class="brand-dot"></span><span class="brand-name">HARLOW RIDGE<span class="brand-sub">Financial Partners</span></span></div>
<nav class="nav">
  <a class="active" href="#">ABOUT US</a><a href="#">SERVICES</a><a href="#">OUR PARTNERS</a><a href="#">PROJECTS</a><a href="#">NEWS</a><a href="#">CONTACT US</a>
</nav>
<div class="abs center welcome">WELCOME TO</div>
<h1 class="abs center hero-title">HARLOW RIDGE FINANCIAL<br>PARTNERS</h1>
<div class="abs btn-hero">LEARN MORE</div>
<div class="abs dots"><span class="on"></span><span></span><span></span><span></span></div>

<svg class="abs" style="left:0;top:660px" width="1200" height="130" viewBox="0 0 1200 130">
  <polygon points="0,105 600,6 1200,105 1200,130 0,130" fill="#9c9c9c"/>
  <polygon points="0,122 600,23 1200,122 1200,130 0,130" fill="#fff"/>
</svg>

<section>
  <div class="abs about-img" role="img" aria-label="City skyline at night in black and white"></div>
  <h2 class="abs heading about-head">ABOUT HARLOW RIDGE</h2>
  <div class="rule" style="left:782px;top:874px"></div>
  <div class="abs about-text">
    <p>Harlow Ridge Financial Partners is an expanding EB-r regional center. We have been successful in sponsoring multiple projects of third-party developers and placing EB-5, B-1, and Private Investments into multiple projects.</p>
    <p>Augiat in pede Fusce tellus Sed metus augue convallis et vehicula ut pulvinar eu ante Integer orci tellus</p>
  </div>
  <div class="abs btn-outline" style="left:717px;top:1086px;width:182px;height:57px;line-height:53px;font-size:16px">LEARN MORE</div>
</section>

<section class="projects"></section>
<h2 class="abs center heading" style="top:1305px;color:#fff">OUR PROJECTS</h2>
<div class="rule" style="top:1354px;background:#bbb"></div>
<div class="abs arrow" style="left:44px;top:1530px">&#8249;</div>
<div class="abs arrow" style="left:1128px;top:1530px">&#8250;</div>
<div class="card" style="left:98px;top:1420px;width:297px;height:281px;background:radial-gradient(ellipse 80px 70px at 75% 8%,rgba(235,235,235,.8),transparent 70%),radial-gradient(ellipse 60px 160px at 25% 45%,rgba(150,150,150,.5),transparent 70%),linear-gradient(180deg,#9a9a9a 0%,#6a6a6a 30%,#3e3e3e 60%,#1c1c1c 100%)" role="img" aria-label="Glass office towers in black and white">
  <div class="cap-title" style="top:192px">PROJECT TITLE</div>
  <div class="cap-text" style="top:218px">Augiat in pede Fusce tellus Sed metus augue convallis et vehicula ut</div>
</div>
<div class="card" style="left:811px;top:1420px;width:297px;height:281px;background:radial-gradient(ellipse 120px 80px at 45% 10%,rgba(240,240,240,.85),transparent 70%),radial-gradient(ellipse 50px 150px at 15% 55%,rgba(60,60,60,.6),transparent 70%),radial-gradient(ellipse 50px 150px at 85% 55%,rgba(60,60,60,.6),transparent 70%),linear-gradient(180deg,#c8c8c8 0%,#8a8a8a 35%,#454545 65%,#1c1c1c 100%)" role="img" aria-label="Curved skyscrapers seen from below">
  <div class="cap-title" style="top:192px">PROJECT TITLE</div>
  <div class="cap-text" style="top:218px">Augiat in pede Fusce tellus Sed metus augue convallis et vehicula ut</div>
</div>
<div class="card" style="left:395px;top:1389px;width:416px;height:343px;background:radial-gradient(ellipse 140px 60px at 25% 12%,rgba(250,250,250,.85),transparent 70%),radial-gradient(ellipse 110px 60px at 70% 6%,rgba(230,230,230,.7),transparent 70%),radial-gradient(ellipse 110px 170px at 70% 55%,rgba(70,70,70,.55),transparent 70%),linear-gradient(180deg,#a8a8a8 0%,#888 28%,#5a5a5a 55%,#2e2e2e 80%,#1a1a1a 100%)" role="img" aria-label="Modern apartment building under a cloudy sky">
  <div class="cap-title" style="top:268px">PROJECT TITLE</div>
  <div class="cap-text" style="top:296px">Augiat in pede Fusce tellus Sed metus augue convallis</div>
</div>

<svg class="abs" style="left:0;top:1770px" width="1200" height="104" viewBox="0 0 1200 104">
  <polygon points="0,80 588,0 1200,80 1200,104 0,104" fill="#8f8f8f"/>
  <polygon points="0,101 588,14 1200,101 1200,104 0,104" fill="#e8e8e8"/>
</svg>

<section class="partners"></section>
<h2 class="abs center heading" style="top:1872px">PARTNER BIOS</h2>
<div class="rule" style="top:1921px"></div>
<div class="abs arrow" style="left:56px;top:2046px">&#8249;</div>
<div class="abs arrow" style="left:1138px;top:2046px">&#8250;</div>
<div class="frame" style="left:144px;top:1986px;width:187px;height:202px"><div class="photo" role="img" aria-label="Portrait photo of a partner" style="background:radial-gradient(ellipse 45px 55px at 50% 40%,rgba(90,90,90,.55),transparent 75%),radial-gradient(ellipse 75px 45px at 50% 100%,rgba(235,235,235,.9),transparent 80%),linear-gradient(180deg,#c9c9c9,#a9a9a9)"></div></div>
<div class="abs p-name" style="left:365px;top:1987px">DANIEL ASHCOMBE</div>
<div class="abs p-text" style="left:365px;top:2024px">Augiat in pede Fusce tellus Sed metus augue convallis et vehicula ut pulvinar eu ante Integer orci tellus tristique vitae consequat nec mauris viverra in gravida eu mattis in ante Morbi eget arcurm</div>
<div class="abs btn-outline" style="left:363px;top:2144px;width:134px;height:40px;line-height:36px;font-size:12.5px">LEARN MORE</div>
<div class="frame" style="left:641px;top:1977px;width:187px;height:202px"><div class="photo" role="img" aria-label="Portrait photo of a partner" style="background:radial-gradient(ellipse 55px 75px at 50% 42%,rgba(45,45,45,.7),transparent 75%),radial-gradient(ellipse 75px 45px at 50% 100%,rgba(70,70,70,.7),transparent 80%),linear-gradient(180deg,#a8a8a8,#8a8a8a)"></div></div>
<div class="abs p-name" style="left:861px;top:1977px">CLARA MENDEN</div>
<div class="abs p-text" style="left:861px;top:2014px">Augiat in pede Fusce tellus Sed metus augue convallis et vehicula ut pulvinar eu ante Integer orci tellus tristique vitae consequat nec mauris viverra in gravida eu mattis in ante Morbi eget arcurm</div>
<div class="abs btn-outline" style="left:858px;top:2135px;width:135px;height:40px;line-height:36px;font-size:12.5px">LEARN MORE</div>

<section>
  <h2 class="abs center heading" style="top:2360px;left:7px">WHAT OUR CLIENT SAYS</h2>
  <div class="rule" style="left:580px;top:2410px"></div>
  <div class="abs center" style="top:2428px;font-family:Georgia,serif;font-size:80px;line-height:1;color:#555;left:4px">&ldquo;</div>
  <div class="abs circle-arrow" style="left:142px;top:2501px"></div>
  <div class="abs circle-arrow" style="left:1022px;top:2501px"></div>
  <svg class="abs" style="left:142px;top:2501px" width="46" height="46"><polyline points="26,15 18,23 26,31" fill="none" stroke="#fff" stroke-width="2"/></svg>
  <svg class="abs" style="left:1022px;top:2501px" width="46" height="46"><polyline points="20,15 28,23 20,31" fill="none" stroke="#fff" stroke-width="2"/></svg>
  <p class="abs quote-text">Nunc tempus felis vitae urna Vivamus porttitor neque at volutpat rutrum purus nisi eleifend libero a tempus libero lectus feugiat felis Morbi diam mauris viverra in gravida eu mattis in anquam Curabitur vel dolor ultrices ipsum dictum</p>
  <div class="abs center" style="top:2600px;font-family:Arial,Helvetica,sans-serif;font-weight:700;font-size:16px;color:#555">DANIEL ASHCOMBE</div>
  <div class="abs btn-black" style="left:492px;top:2656px;width:220px;height:52px;line-height:52px">VIEW MORE STORIES</div>
</section>

<section class="contact" role="img" aria-label="Aerial black and white photo of a dense city skyline"></section>
<h2 class="abs center heading" style="top:2834px;color:#111">CONTACT FORM</h2>
<div class="rule" style="top:2884px;background:#111"></div>
<div class="field" style="left:241px;top:2913px;width:351px;height:50px">Name:</div>
<div class="field" style="left:608px;top:2913px;width:352px;height:50px">Phone:</div>
<div class="field" style="left:241px;top:2981px;width:351px;height:50px">Email:</div>
<div class="field" style="left:608px;top:2981px;width:352px;height:50px">Subject:</div>
<div class="field" style="left:241px;top:3048px;width:719px;height:103px;padding-top:14px">Message:</div>
<div class="abs btn-black" style="left:516px;top:3180px;width:172px;height:49px;line-height:49px;font-family:'Ubuntu',Arial,sans-serif;font-weight:500;font-size:19px;background:#1a1a1a">SUBMIT</div>

<svg class="abs" style="left:0;top:3240px" width="1200" height="263" viewBox="0 0 1200 263">
  <polygon points="0,0 600,90 1200,0 1200,263 0,263" fill="#3a3a3a"/>
  <polygon points="0,12 600,102 1200,12 1200,263 0,263" fill="#050505"/>
</svg>
<nav class="abs center footer-nav">
  <a href="#">ABOUT US</a><a href="#">SERVICES</a><a href="#">OUR PARTNERS</a><a href="#">PROJECTS</a><a href="#">NEWS</a><a href="#">CONTACT US</a>
</nav>
<div class="abs center" style="top:3402px;font-family:Arial,Helvetica,sans-serif;font-size:13px;color:#bbb">&copy; 2020 Company Name | All Rights Reserved</div>
<div class="abs social"><span></span><span></span><span></span></div>

</body>
</html>
```